Tide & Thistle Website Creation For Online Spirits Sales via MerrowVats.com

Want a Website developed that I will use to partner with Merrow Vats to sell my signature rum online. Merrow Vats will add the final code to make the website an e-commerce site. Website should have links to Social media pages, recipies, About, news and events, products. I have he domain name already just need a designer to make the website look professional. Need website capable of being viewed on iPhone and Android devices. Please use the color scheme that is on the label. The brand motto is: Celebrate Life With Family old and new friends. The bottle sent in the images will be replaced with and actual high resolution image of the bottle when it is produce on 27 DEC 21. Can give the selected designer access to develop the website. I have the hostbramble.com domain name. Final code will be added by a designer from MerrowVats.com to make it a e-commerce store.
Updates

I added more information to refine the design I wanted. I should have had this information available to the designers when I started the project.

Target Market(s)

Target Market is 25-50 year old who drink rum

Industry/Entity Type

Spirits. Using Website to sell Rum online

Number of Pages Required

1 page

Font styles to use
Sans Serif

Colors
00AB8E
00BBA5
67D7C9
C6EFE9
E9F9F6

Requirements
Must have
• Must look elegant and of high class. Rum is being market as a premium unnamed rum.
Nice to have
• Video of people drinking, smiling and celebrating

```html
<!DOCTYPE html>
<html lang="en">
<head>
<meta charset="utf-8">
<title>Tide &amp; Thistle</title>
<link href="https://fonts.googleapis.com/css2?family=Cinzel:wght@600;700&family=Lato:wght@400;700&family=Open+Sans:wght@400;600&display=swap" rel="stylesheet">
<style>
:root{
  --green:#1a9e7c;
  --green-bright:#00ab8e;
  --teal:#00bba5;
  --mint:#67d7c9;
  --mint-pale:#c6efe9;
  --mint-mist:#e9f9f6;
  --solutions-bg:#a9dcd4;
  --ink:#1c1c1c;
  --body:#333333;
  --white:#ffffff;
  --black:#000000;
}
*{margin:0;padding:0;box-sizing:border-box}
html,body{width:1200px;height:3304px;overflow:hidden}
body{position:relative;background:var(--white);font-family:'Lato',sans-serif;color:var(--body)}
.heading{font-family:'Cinzel',serif;font-weight:700;color:var(--ink)}
section,header,footer{position:absolute;left:0;width:1200px}
.abs{position:absolute}
.btn{position:absolute;display:flex;align-items:center;justify-content:center;background:var(--green);color:var(--white);font-family:'Cinzel',serif;font-weight:700;font-size:14px;box-shadow:0 3px 6px rgba(0,0,0,.2)}

/* header */
.site-header{top:0;height:114px;background:var(--white);border-top:5px solid var(--green)}
.brand{position:absolute;left:112px;top:14px;width:170px;text-align:center}
.brand-dot{width:46px;height:46px;border-radius:50%;background:var(--ink);margin:0 auto 4px}
.brand-name{font-family:'Cinzel',serif;font-weight:600;font-size:20px;color:var(--ink);white-space:nowrap}
.nav a{position:absolute;top:48px;font-family:'Open Sans',sans-serif;font-size:15px;color:var(--ink);text-decoration:none}
.nav a.active{color:var(--green);font-weight:600;border-bottom:3px solid var(--green);padding:0 4px 8px;top:48px}
.nav-contact{left:855px;top:41px;width:96px;height:33px;font-size:14px}
.user-badge{left:968px;top:44px;width:28px;height:28px;border-radius:50%;background:var(--green)}
.social{display:flex;gap:7px}
.social span{width:11px;height:11px;border-radius:2px;background:var(--ink)}

/* hero */
.hero{top:114px;height:585px;background:linear-gradient(180deg,#3d4a3a 0%,#8a7a4e 22%,#4f5a33 40%,#2f4520 65%,#1f3015 100%)}
.hero-title{left:113px;top:318px;font-size:42px;color:var(--white);letter-spacing:.5px}
.hero-text{left:112px;top:378px;font-size:15.5px;line-height:28px;color:var(--white)}
.hero-btn{left:113px;top:452px;width:123px;height:33px}
.play{left:576px;top:389px;width:48px;height:48px;border-radius:50%;background:var(--green);border:4px solid rgba(255,255,255,.25)}
.bottle{left:820px;top:180px;width:135px;height:397px;border-radius:30px 30px 40px 40px;background:linear-gradient(180deg,#d9ddd0 0%,#b98a3a 30%,#c7913c 70%,#9b6b28 100%)}
.hero-curve{left:0;bottom:0;width:1200px;height:110px}

/* about */
.about{top:699px;height:507px}
.about-title{left:156px;top:130px;font-size:30px}
.about-title em{font-style:normal;color:var(--green)}
.about-text{left:156px;top:180px;width:500px;font-size:15.5px;line-height:28.3px}
.about-btn{left:156px;top:366px;width:124px;height:34px}
.emblem{left:733px;top:115px;width:308px;height:308px;border-radius:50%;background:var(--green);border:12px solid var(--white);box-shadow:0 0 0 8px var(--green),0 8px 18px rgba(0,0,0,.25)}

/* solutions */
.solutions{top:1206px;height:698px;background:linear-gradient(180deg,var(--solutions-bg) 0%,#a3d8cf 100%)}
.section-title{width:1200px;text-align:center;font-size:31px}
.solutions .section-title{top:76px}
.card{position:absolute;top:167px;width:230px;height:415px;background:var(--white);text-align:center;box-shadow:0 2px 6px rgba(0,0,0,.08)}
.card-photo{height:159px}
.card-icon{position:absolute;left:83px;top:123px;width:64px;height:64px;border-radius:50%;background:var(--green);border:4px solid var(--white);display:flex;align-items:center;justify-content:center}
.card h3{position:absolute;top:211px;width:100%;font-family:'Cinzel',serif;font-weight:700;font-size:18.5px;color:var(--ink)}
.card p{position:absolute;top:245px;width:100%;padding:0 10px;font-size:14.5px;line-height:27.5px}
.read-more{position:absolute;top:357px;width:100%;font-family:'Open Sans',sans-serif;font-weight:600;font-size:14.5px;color:var(--green)}

/* testimonials */
.testimonials{top:1904px;height:519px}
.testimonials .section-title{top:78px}
.portrait-ring{left:155px;top:180px;width:316px;height:316px;border-radius:50%;background:var(--mint-pale);box-shadow:0 2px 8px rgba(0,0,0,.15)}
.portrait{left:168px;top:193px;width:290px;height:290px;border-radius:50%;background:radial-gradient(circle at 50% 45%,#2fae8c 0%,var(--green) 70%)}
.quote-name{left:546px;top:182px;font-size:20px}
.quote-mark{left:548px;top:212px;font-family:Georgia,serif;font-size:64px;line-height:64px;color:#b9bdbc;font-weight:700}
.quote-text{left:550px;top:268px;width:500px;font-size:15.5px;line-height:28.3px}
.quote-btn{left:547px;top:398px;width:129px;height:38px;border:3px solid var(--ink);font-family:'Cinzel',serif;font-weight:700;font-size:14px;color:var(--ink);display:flex;align-items:center;justify-content:center}

/* blog */
.blog{top:2423px;height:587px;background:linear-gradient(180deg,var(--mint-pale) 0%,#d5f3ec 45%,#c8e9dd 100%)}
.blog .section-title{top:74px}
.post{position:absolute;top:167px;width:298px;height:329px;background:var(--white);text-align:center}
.post-photo{height:195px}
.post h3{position:absolute;top:220px;width:100%;font-family:'Cinzel',serif;font-weight:700;font-size:18px;line-height:28px;color:var(--ink)}
.post-meta{position:absolute;top:282px;width:100%;display:flex;justify-content:center;gap:26px;font-family:'Open Sans',sans-serif;font-size:14px;color:var(--ink)}
.post-meta span{display:flex;align-items:center;gap:6px}

/* footer */
.site-footer{top:3010px;height:294px;background:var(--black);color:var(--white)}
.footer-dot{left:174px;top:50px;width:52px;height:52px;border-radius:50%;background:var(--white)}
.footer-name{left:112px;top:110px;font-family:'Cinzel',serif;font-weight:600;font-size:27px;color:var(--white)}
.footer-links{left:111px;top:164px;font-family:'Open Sans',sans-serif;font-size:15px;word-spacing:3px}
.footer-links i{font-style:normal;margin:0 10px}
.news-title{left:728px;top:53px;font-size:19px;color:var(--white)}
.news-text{left:728px;top:83px;font-size:15.5px}
.news-form{left:728px;top:113px;width:360px;height:37px;border:2px solid var(--white);display:flex}
.news-input{flex:1;font-family:'Open Sans',sans-serif;font-size:13px;padding:9px 10px}
.news-submit{width:94px;background:var(--white);color:var(--black);font-family:'Open Sans',sans-serif;font-weight:600;font-size:15px;display:flex;align-items:center;justify-content:center}
.footer-rule{left:112px;top:205px;width:976px;height:1px;background:#444}
.copyright{left:112px;top:228px;font-size:15.5px}
.footer-social{left:1006px;top:235px}
.footer-social span{background:var(--white)}
</style>
</head>
<body>

<header class="site-header">
  <div class="brand">
    <div class="brand-dot"></div>
    <div class="brand-name">Tide &amp; Thistle</div>
  </div>
  <nav class="nav">
    <a class="active" href="#" style="left:342px;top:48px">Home</a>
    <a href="#" style="left:424px">Recipes</a>
    <a href="#" style="left:516px">About Us</a>
    <a href="#" style="left:615px">News</a>
    <a href="#" style="left:690px">Events</a>
    <a href="#" style="left:773px">Products</a>
  </nav>
  <div class="btn nav-contact">Contact</div>
  <div class="abs user-badge"></div>
  <div class="abs social" style="left:1013px;top:53px"><span></span><span></span><span></span><span></span></div>
</header>

<section class="hero">
  <div class="abs" role="img" aria-label="Sugar cane field at sunset" style="inset:0"></div>
  <h1 class="abs heading hero-title">Welcome to Tide &amp; Thistle</h1>
  <p class="abs hero-text">Lorem ipsum dolor sit amet, consectetur adipiscing elit,<br>ut labore et dolore magna aliqua. Ut enim ad minim veniam,</p>
  <div class="btn hero-btn">Get Started</div>
  <div class="abs play">
    <svg width="40" height="40" viewBox="0 0 40 40"><path d="M15 11 L29 20 L15 29Z" fill="#fff"/></svg>
  </div>
  <div class="abs bottle" role="img" aria-label="Tide &amp; Thistle rum bottle"></div>
  <svg class="abs hero-curve" viewBox="0 0 1200 110" preserveAspectRatio="none">
    <path d="M0 110 L0 100 C60 70 120 62 200 60 C260 58 300 40 330 42 C380 30 420 55 470 50 C540 40 580 25 640 20 C720 15 760 40 840 38 C920 42 980 30 1060 35 C1120 40 1160 42 1200 40 L1200 110Z" fill="#fff"/>
  </svg>
</section>

<section class="about">
  <h2 class="abs heading about-title">About To <em>Tide &amp; Thistle</em></h2>
  <p class="abs about-text">Lorem ipsum dolor sit amet, consectetur adipiscing elit, sed do eiusmod tempor incididunt ut labore et dolore magna aliqua. Ut enim ad minim veniam, quis nostrud exercitation ullamco laboris nisi ut aliquip ex ea commodo consequat.Sed ut perspiciatis unde omnis iste natus error sit voluptatem accusantium doloremque laudantium, totam rem aperiam,</p>
  <div class="btn about-btn">Read More</div>
  <div class="abs emblem"></div>
</section>

<section class="solutions">
  <h2 class="abs heading section-title">Our Solutions</h2>

  <article class="card" style="left:112px">
    <div class="card-photo" role="img" aria-label="White product tins" style="background:linear-gradient(135deg,#f1f1f1,#bdbdbd)"></div>
    <div class="card-icon"><svg width="30" height="30" viewBox="0 0 30 30" fill="none" stroke="#fff" stroke-width="2"><path d="M5 15 L15 5 H25 V15 L15 25Z"/><circle cx="20" cy="10" r="2"/></svg></div>
    <h3>White-Label</h3>
    <p>Lorem ipsum dolor sit amet, consectetur adipiscing elit, sed do eiusmod tempor incididunt ut labore et dolore</p>
    <div class="read-more">Read More ›</div>
  </article>

  <article class="card" style="left:360px">
    <div class="card-photo" role="img" aria-label="Person reading a subscription screen" style="background:linear-gradient(135deg,#3b5a8a,#d8c7b4)"></div>
    <div class="card-icon"><svg width="30" height="30" viewBox="0 0 30 30" fill="none" stroke="#fff" stroke-width="2"><circle cx="15" cy="15" r="10"/><path d="M15 9 V15 L19 18"/></svg></div>
    <h3>Subscriptions</h3>
    <p>Lorem ipsum dolor sit amet, consectetur adipiscing elit, sed do eiusmod tempor incididunt ut labore et dolore</p>
    <div class="read-more">Read More ›</div>
  </article>

  <article class="card" style="left:609px">
    <div class="card-photo" role="img" aria-label="Team meeting around a table" style="background:linear-gradient(135deg,#2a2c30,#6a5f58)"></div>
    <div class="card-icon"><svg width="30" height="30" viewBox="0 0 30 30" fill="none" stroke="#fff" stroke-width="2"><rect x="5" y="6" width="20" height="14"/><path d="M10 16 V12 M15 16 V9 M20 16 V13 M11 25 H19 M15 20 V25"/></svg></div>
    <h3>Analytics Suite</h3>
    <p>Lorem ipsum dolor sit amet, consectetur adipiscing elit, sed do eiusmod tempor incididunt ut labore et dolore</p>
    <div class="read-more">Read More ›</div>
  </article>

  <article class="card" style="left:858px">
    <div class="card-photo" role="img" aria-label="Direct marketing concept" style="background:linear-gradient(135deg,#1b2c55,#5c7fb0)"></div>
    <div class="card-icon"><svg width="30" height="30" viewBox="0 0 30 30" fill="none" stroke="#fff" stroke-width="2"><rect x="6" y="12" width="18" height="12"/><path d="M6 12 L15 19 L24 12 M15 4 V10 M12 7 L15 4 L18 7"/></svg></div>
    <h3>Direct Marketing</h3>
    <p>Lorem ipsum dolor sit amet, consectetur adipiscing elit, sed do eiusmod tempor incididunt ut labore et dolore</p>
    <div class="read-more">Read More ›</div>
  </article>
</section>

<section class="testimonials">
  <h2 class="abs heading section-title">Testimonials</h2>
  <div class="abs portrait-ring"></div>
  <div class="abs portrait" role="img" aria-label="Portrait of a smiling customer"></div>
  <h3 class="abs heading quote-name">Arlo Penn</h3>
  <div class="abs quote-mark">“</div>
  <p class="abs quote-text">Lorem ipsum dolor sit amet, consectetur adipiscing elit, sed do eiusmod tempor incididunt ut labore et dolore magna aliqua. Ut enim ad minim veniam, quis nostrud exercitation ullamco laboris nisi ut aliquip ex ea commodo consequat.</p>
  <div class="abs quote-btn">Read More</div>
</section>

<section class="blog">
  <h2 class="abs heading section-title">Our Blog</h2>

  <article class="post" style="left:112px">
    <div class="post-photo" role="img" aria-label="Friends toasting with glasses of rum" style="background:linear-gradient(135deg,#3a2a22,#8c6a4e)"></div>
    <h3>Lorem ipsum dolor sit<br>amet, consectetur</h3>
    <div class="post-meta"><span>▦ 14.12.2021</span><span>● ( 0 ) Comments</span></div>
  </article>

  <article class="post" style="left:451px">
    <div class="post-photo" role="img" aria-label="Friends laughing at a bar table" style="background:linear-gradient(135deg,#2e2e2c,#7a6a58)"></div>
    <h3>Lorem ipsum dolor sit<br>amet, consectetur</h3>
    <div class="post-meta"><span>▦ 14.12.2021</span><span>● ( 0 ) Comments</span></div>
  </article>

  <article class="post" style="left:790px">
    <div class="post-photo" role="img" aria-label="Bartender serving a drink" style="background:linear-gradient(135deg,#5a2a1a,#c08a4a)"></div>
    <h3>Lorem ipsum dolor sit<br>amet, consectetur</h3>
    <div class="post-meta"><span>▦ 14.12.2021</span><span>● ( 0 ) Comments</span></div>
  </article>
</section>

<footer class="site-footer">
  <div class="abs footer-dot"></div>
  <div class="abs footer-name">Tide &amp; Thistle</div>
  <div class="abs footer-links">Home<i>|</i>Recipes<i>|</i>About Us<i>|</i>News<i>|</i>Events<i>|</i>Products</div>
  <h3 class="abs heading news-title">Nwesletter</h3>
  <p class="abs news-text">Lorem ipsum dolor sit amet, consectetur</p>
  <div class="abs news-form"><div class="news-input">Email Address</div><div class="news-submit">SUBMIT</div></div>
  <div class="abs footer-rule"></div>
  <p class="abs copyright">©Copyrights 2021Tide &amp; Thistle| All Rights Reserved</p>
  <div class="abs social footer-social"><span></span><span></span><span></span><span></span></div>
</footer>

</body>
</html>
```